Corporate Design für Steuerkanzlei
Zielgruppe
Wir sind eine Steuerkanzlei im (ländlichen) Neustadt an der Donau, die seit über 30 Jahren von Herrn Konrad (Vater) Wehrle geführt wird. Mit Einstieg durch Herrn Florian (Sohn) Wehrle haben wir die Wehrle Steuerberatungsgellschaft mbH gegründet und suchen deshalb ein neues Kanzleilogo / Geschäftspapiere. Wir betreuen/beraten kleine Unternehmen und Privatpersonen aus der Region und haben derzeitig 14 Angestellte.
Aufgabenstellung
Das Design sollte in erster Linie seriös und nicht verspielt wirken. Einer vertrauensvollen Steuerberaterungskanzlei entsprechend. Dennoch sind wir auch für eine moderne Gestaltung offen.

```html
<!DOCTYPE html>
<html lang="de">
<head>
<meta charset="utf-8">
<title>Wehrle Steuerberatungsgesellschaft mbH – Geschäftsausstattung</title>
<link rel="stylesheet" href="https://fonts.googleapis.com/css2?family=Oswald:wght@300;400;500&family=Open+Sans:wght@400;700&family=Roboto:wght@400&display=swap">
<style>
  :root {
    --backdrop: #e6e8eb;
    --paper: #ffffff;
    --brand-dark: #0d4656;
    --brand: #177a8c;
    --ink: #2b2b2b;
    --ink-soft: #444;
  }
  * { margin: 0; padding: 0; box-sizing: border-box; }
  html, body { width: 1200px; height: 848px; overflow: hidden; }
  body { background: var(--backdrop); position: relative; font-family: 'Open Sans', sans-serif; }

  .sheet, .card { position: absolute; background: var(--paper); box-shadow: 0 4px 14px rgba(0,0,0,.18); }

  /* Wordmark */
  .wordmark { display: flex; align-items: center; gap: 7px; color: var(--brand-dark); }
  .wordmark__square { flex: none; border: 3px solid currentColor; }
  .wordmark__text { display: block; font-family: 'Oswald', sans-serif; font-weight: 500; line-height: 1; letter-spacing: .06em; }
  .wordmark__sub { display: block; font-family: 'Oswald', sans-serif; font-weight: 300; letter-spacing: .05em; white-space: nowrap; }

  /* Letterhead */
  .letterhead { left: 172px; top: 64px; width: 509px; height: 720px; }
  .letterhead__brand { position: absolute; right: 32px; top: 30px; }
  .letterhead__brand .wordmark__square { width: 26px; height: 26px; }
  .letterhead__brand .wordmark__text { font-size: 22px; }
  .letterhead__brand .wordmark__sub { font-size: 7.4px; margin-top: 1px; color: var(--brand); }
  .sender-line { position: absolute; left: 54px; top: 111px; font-family: 'Roboto', sans-serif; font-size: 5.6px; color: var(--brand-dark); border-bottom: .7px solid var(--brand); padding-bottom: 1px; }
  .recipient { position: absolute; left: 55px; top: 130px; font-family: 'Roboto', sans-serif; font-size: 8.2px; line-height: 10.4px; color: var(--ink); font-style: normal; }
  .recipient .city { margin-top: 10px; }
  .letter-body { position: absolute; left: 55px; top: 245px; width: 276px; font-size: 7.9px; line-height: 9.26px; color: var(--ink-soft); }
  .letter-body .subject { font-weight: 700; color: var(--ink); margin-bottom: 20px; }
  .letter-body p { margin-bottom: 9px; }
  .letter-body .tight { margin-bottom: 0; }
  .signature { display: block; width: 108px; height: 20px; margin: 8px 0 6px; background: linear-gradient(90deg, #e9ecee, #f4f5f6); border-radius: 3px; }
  .letter-footer { position: absolute; left: 48px; top: 676px; height: 44px; display: flex; }
  .letter-footer__col { border-left: 1px solid var(--brand); padding: 2px 0 0 7px; font-family: 'Oswald', sans-serif; font-weight: 400; font-size: 6.6px; line-height: 10.3px; letter-spacing: .1em; color: var(--brand-dark); }
  .letter-footer__col:nth-child(1) { width: 119px; }
  .letter-footer__col:nth-child(2) { width: 129px; }

  /* Business cards */
  .card--front { left: 768px; top: 198px; width: 272px; height: 176px; }
  .card--front .wordmark { position: absolute; left: 22px; top: 21px; }
  .card--front .wordmark__square { width: 38px; height: 38px; border-width: 4px; }
  .card--front .wordmark__text { font-size: 29px; }
  .card--front .wordmark__sub { font-size: 9.6px; margin-top: 2px; color: var(--brand); }
  .card__rule { position: absolute; left: 58px; top: 78px; bottom: 0; border-left: 1.2px solid var(--brand); }
  .card__contact { position: absolute; left: 71px; top: 78px; font-family: 'Oswald', sans-serif; font-weight: 300; font-size: 9px; line-height: 11.2px; letter-spacing: .06em; color: var(--brand-dark); }
  .card__contact .name { font-weight: 400; color: var(--brand); }
  .card__contact .gap { margin-top: 3px; }
  .card__contact .label { color: var(--brand); }
  .card__contact .dot { display: inline-block; width: 3px; height: 3px; background: var(--brand-dark); vertical-align: middle; margin: 0 4px; }
  .card__contact .web { font-weight: 500; margin-top: 3px; color: var(--brand); }

  .card--back { left: 766px; top: 475px; width: 275px; height: 178px; background: var(--brand); display: flex; align-items: center; justify-content: center; }
  .card--back .wordmark { color: #fff; }
  .card--back .wordmark__square { width: 30px; height: 30px; }
  .card--back .wordmark__text { font-size: 22px; }
  .card--back .wordmark__sub { font-size: 7.6px; margin-top: 2px; }
</style>
</head>
<body>

<section class="sheet letterhead" aria-label="Briefbogen">
  <div class="wordmark letterhead__brand">
    <span class="wordmark__square"></span>
    <div>
      <span class="wordmark__text">Wehrle</span>
      <span class="wordmark__sub">Steuerberatungsgesellschaft mbH</span>
    </div>
  </div>

  <div class="sender-line">Max Mustermann, Musterstr. 123, 12345 Musterstadt</div>

  <address class="recipient">
    Martina Musterfrau<br>Musterstraße 456
    <div class="city">12345 Berlin</div>
  </address>

  <div class="letter-body">
    <div class="subject">Quidero molore, atatur sae. Nequat,</div>
    <p>Ur sit, imus, ipicatem voluptate eum re dolluptios sequosam, eum reritati am volor sapedissi quo blaboribust, sequass itasped igendi cus exerfer feruptas iusanda ndaest, qui omnis nus aut fugitinis quatur ad ullaut mostem quasperiae corem et aciatem illatin ciduntores quidis utemquam autemperae soluptiae lab illacescia solorum et fugiam ratatatus exerro blaciis samusam etur? Uga. Neque nam simi, nest, ommod essedios magnatia nossi aute nonsequam fugiaspis moluptas sed el int etur saepe nonsecatem excea noneceperrum ulligendit faccullores et lantur si ium at.Ota cuptae non ea de opta voles rem rae dolore ilia vellab isi blanis idit veribus auda alit labore desenis imenis que in con rehent, explat ped que volorum, autent, si tetur?</p>
    <p class="tight">Ihil ium restior ecepero reptistius es aborepe diatiunt dignis diciae voluptu ribearit, que nat aute et as maximus, qui blab iur aut volest, nonsequae odios doluptatiae velignimin perescia vent.</p>
    <p>Pa voluptas expero corectur molest eaquid enda vidus verciis quodi te dit aliquid unturem poreper feratur? Quis aut rehenihilit et quam, eris et perorru mquamusa quo et untia volupie nisimoluptae esseribus cora doluptati doluptatur atisciumqui re pa quat aut lam solescia intiis et millabor sit odis et quos re sam, vendicientur abo. Equi totatus rest, nosam quodi omni doloriosam des ea nimpelique volo elendae dellign ihilitis solupta temporp orupta iuntia ipiste natibusapis volesedis reriori taerrup tatiberes nobitiur, sequi omnihillab id maximagnat omnimus dolo quunt, int aut earum lacit peliquunt iduciet, id que autemolum deruptati te non re.</p>
    <p class="tight">Sincerely</p>
    <span class="signature" role="img" aria-label="Handschriftliche Unterschrift"></span>
    <p>Max Mustermann</p>
  </div>

  <footer class="letter-footer">
    <div class="letter-footer__col">Max Mustermann<br>Musterstr. 123<br>12345 Musterstadt</div>
    <div class="letter-footer__col">T: 020 / 987 654 321<br>F: 020 / 987 654 322<br>info@beispielbuero.de</div>
    <div class="letter-footer__col">Beispielbank GmbH<br>IBAN: DE98765432100<br>BIC: BSP720KX10</div>
  </footer>
</section>

<section class="card card--front" aria-label="Visitenkarte Vorderseite">
  <div class="wordmark">
    <span class="wordmark__square"></span>
    <div>
      <span class="wordmark__text">Wehrle</span>
      <span class="wordmark__sub">Steuerberatungsgesellschaft mbH</span>
    </div>
  </div>
  <span class="card__rule"></span>
  <div class="card__contact">
    <div class="name">Max Mustermann</div>
    <div>Geschäftsführer</div>
    <div class="gap">Musterstr. 123<span class="dot"></span>12345 Musterstadt</div>
    <div class="gap"><span class="label">T:</span> 020 / 987 654 321 &nbsp; <span class="label">F:</span> 020 / 987 654 323</div>
    <div>info@beispielnetz.de</div>
    <div class="web">www.beispielnetz.de</div>
  </div>
</section>

<section class="card card--back" aria-label="Visitenkarte Rückseite">
  <div class="wordmark">
    <span class="wordmark__square"></span>
    <div>
      <span class="wordmark__text">Wehrle</span>
      <span class="wordmark__sub">Steuerberatungsgesellschaft mbH</span>
    </div>
  </div>
</section>

</body>
</html>
```